Business Card Re-Design/Update

We'd like to update out business cards. I've included our current "Style guide" which has the colour scheme of the organisation in it. I've also included the branding files with logos etc in them.

I've also included a copy of one of our existing cards so that you can see how ugly/dated they look. I'd like a fresh modern corporate look.

Target Market(s)

These are for our clients, potential clients, industry contacts - like all business cards

Contact Information for Business Card

Name
Position
Company Address - Level 1, 47 Fernby Street, Carlow Qld 4072
Direct Phone
mobile
Email
Website -www.korvalit.com.au
Logo

Colors

Designer to choose colors to be used in the design.

Requirements
Must have
• Main Logo
• Cards will need to be editable to be able to personalize them for each new employee.
Nice to have
• The MapOut, ShipWell, KeepSteady would be okay to have if they can be sensibly and professionally added to the look without detracting from the main imagery.
• Maybe they could go on the back of the card? will leave this to your creative discretion as to whether/where they fit.
Should not have
• Should not have decorative or script fonts

```html
<!DOCTYPE html>
<html lang="en">
<head>
<meta charset="utf-8">
<title>korvalIT business card</title>
<link rel="stylesheet" href="https://fonts.googleapis.com/css2?family=Arimo:wght@400;700&display=swap">
<style>
  :root {
    --bg: #e4e4e4;
    --card: #f7f7f7;
    --red: #c4161c;
    --red-dark: #8e0b10;
    --ink: #1f1f1f;
    --muted: #555555;
    --green: #5a9c3a;
    --blue: #1e86c8;
    --magenta: #b31d8a;
    --white: #ffffff;
  }
  * { box-sizing: border-box; margin: 0; padding: 0; }
  html, body {
    width: 1200px; height: 960px; overflow: hidden;
    background: var(--bg);
    font-family: "Arimo", Arial, sans-serif;
  }
  .canvas { position: relative; width: 1200px; height: 960px; }
  .card {
    position: absolute; width: 600px; height: 343px;
    background: var(--card);
    box-shadow: 0 2px 4px rgba(0,0,0,0.25);
    overflow: hidden;
  }
  .card--front { left: 314px; top: 113px; }
  .card--back { left: 311px; top: 472px; }

  .person { position: absolute; left: 41px; top: 51px; }
  .person__name { font-size: 20px; font-weight: 700; color: var(--red); letter-spacing: 0.2px; line-height: 22px; }
  .person__role { font-size: 15px; color: var(--ink); margin-top: 2px; line-height: 18px; }

  .brand {
    position: absolute; right: 34px; top: 54px;
    display: flex; align-items: center; gap: 10px;
  }
  .brand__mark { width: 26px; height: 26px; background: var(--red); }
  .brand__name { font-size: 30px; font-weight: 700; color: var(--red); letter-spacing: -0.5px; }

  .band {
    position: absolute; left: 0; top: 134px; width: 600px; height: 171px;
    background: linear-gradient(135deg, #d01a20 0%, #a80e14 45%, var(--red-dark) 100%);
  }
  .band__feature {
    position: absolute; left: 50px; top: 0; width: 210px; height: 171px;
    background: linear-gradient(90deg, rgba(90,156,58,0.55) 0%, rgba(30,134,200,0.55) 50%, rgba(179,29,138,0.55) 100%);
  }

  .contact {
    position: absolute; right: 30px; top: 148px;
    text-align: right; color: var(--white); font-size: 14px; line-height: 18px;
    font-style: normal;
  }
  .contact__address { margin-bottom: 12px; }
  .contact__line { line-height: 19px; }
  .contact__label { font-weight: 700; }

  .website {
    position: absolute; right: 30px; top: 316px;
    font-size: 14px; color: var(--muted); letter-spacing: 2.4px;
  }

  .back-brand {
    position: absolute; left: 0; right: 0; top: 110px;
    display: flex; justify-content: center; align-items: center; gap: 16px;
  }
  .back-brand__mark { width: 52px; height: 52px; background: var(--red); }
  .back-brand__name { font-size: 58px; font-weight: 700; color: var(--red); letter-spacing: -1px; }

  .services {
    position: absolute; left: 46px; top: 278px;
    display: flex; gap: 38px; align-items: center;
  }
  .service { display: flex; align-items: center; gap: 8px; font-size: 25px; font-weight: 700; }
  .service__mark { width: 18px; height: 18px; }
  .service--map { color: var(--green); }
  .service--map .service__mark { background: var(--green); }
  .service--ship { color: var(--blue); }
  .service--ship .service__mark { background: var(--blue); }
  .service--keep { color: var(--magenta); }
  .service--keep .service__mark { background: var(--magenta); }
</style>
</head>
<body>
<main class="canvas">
  <section class="card card--front">
    <div class="person">
      <p class="person__name">MAREN HOLLOWAY</p>
      <p class="person__role">Business Development Manager</p>
    </div>
    <div class="brand">
      <span class="brand__mark"></span>
      <span class="brand__name">korvalIT</span>
    </div>

    <div class="band">
      <div class="band__feature" role="img" aria-label="Decorative stripe graphic in green, blue and magenta on the red band"></div>
    </div>

    <address class="contact">
      <p class="contact__address">Level 1, 47 Fernby Street<br>Carlow Qld 4072</p>
      <p class="contact__line"><span class="contact__label">P:</span> +61 (0)7 3900 4120</p>
      <p class="contact__line"><span class="contact__label">P:</span> +61 (0)7 3900 4127</p>
      <p class="contact__line"><span class="contact__label">C:</span> +61 (0)412 555 018</p>
      <p class="contact__line"><span class="contact__label">F:</span> +61 (0)7 3900 4199</p>
      <p class="contact__line"><span class="contact__label">E:</span> mholloway@korvalit.com.au</p>
    </address>

    <p class="website">www.korvalit.com.au</p>
  </section>

  <section class="card card--back">
    <div class="back-brand">
      <span class="back-brand__mark"></span>
      <span class="back-brand__name">korvalIT</span>
    </div>
    <div class="services">
      <p class="service service--map"><span class="service__mark"></span>MapOut</p>
      <p class="service service--ship"><span class="service__mark"></span>ShipWell</p>
      <p class="service service--keep"><span class="service__mark"></span>KeepSteady</p>
    </div>
  </section>
</main>
</body>
</html>
```